Medical Skincare services/menu/pricing Booklet 12 pages

We need produce a 12-page glossy, saddle-stitched booklet (5 1/2" tall X 81/2" wide). The booklet will be used as a services menu for a skin care salon. I have mocked up the booklet (w/ all copy) in WORD and I've provided a separate PDF of the accurate page order (see files attached). IMPORTANT: Feel free to use your creativity yet style-wise it should kinda match my wife's website colors and text style. Her clients are demanding so she wants a clean, high end, modern look (ala Apple maybe?). See her website for a frame of reference www.GlowWithMara.com
Updates

Target Market(s)

upscale female, professional women, teens with acne

Industry/Entity Type

Medical

Requirements
Must have
• the pics in the mock up are important. I've attached them here

```html
<!DOCTYPE html>
<html lang="en">
<head>
<meta charset="utf-8">
<title>Glow by Mara — Services Menu Cover</title>
<link href="https://fonts.googleapis.com/css2?family=Nunito+Sans:wght@300;700&display=swap" rel="stylesheet">
<style>
  :root {
    --ink: #000000;
    --paper: #ffffff;
    --silver: #c9c9cb;
    --menu-grey: #a9abad;
    --taupe: #b2a48e;
  }
  * { margin: 0; padding: 0; box-sizing: border-box; }
  html, body { width: 1200px; height: 846px; overflow: hidden; background: var(--paper); }
  .cover {
    position: relative;
    width: 1200px;
    height: 846px;
    font-family: "Nunito Sans", Arial, sans-serif;
  }
  .cover__hero {
    position: absolute;
    left: 0; top: 0;
    width: 1200px; height: 688px;
    background: var(--ink);
    display: flex;
    align-items: center;
    justify-content: center;
  }
  .brand-name {
    color: var(--silver);
    font-weight: 700;
    font-size: 104px;
    letter-spacing: 2px;
    text-transform: uppercase;
    line-height: 1;
    margin-top: -8px;
  }
  .cover__rule {
    position: absolute;
    left: 0; top: 688px;
    width: 1200px; height: 5px;
    background: var(--taupe);
  }
  .service-list {
    position: absolute;
    left: 618px; top: 711px;
    list-style: none;
    color: var(--menu-grey);
    font-weight: 300;
    font-size: 20.5px;
    line-height: 35.5px;
    white-space: nowrap;
  }
  .service-list .dot {
    display: inline-block;
    width: 9px; height: 9px;
    margin: 0 14px 2px;
    border-radius: 50%;
    background: var(--menu-grey);
    vertical-align: middle;
  }
</style>
</head>
<body>
  <main class="cover">
    <section class="cover__hero">
      <h1 class="brand-name">Glow by Mara</h1>
    </section>
    <div class="cover__rule"></div>
    <ul class="service-list">
      <li>HydraPure MD<span class="dot"></span>Laser Renewal<span class="dot"></span>IPL (Brightlight)</li>
      <li>Vascular<span class="dot"></span>Microneedling MD<span class="dot"></span>LED Light Therapy</li>
      <li>Vita Peel<span class="dot"></span>Customized Facials &amp; Peels<span class="dot"></span>Dermaplane</li>
    </ul>
  </main>
</body>
</html>
```